Lotus Market Hall VIP Card(Magnetic strip plastic card)

We need Fancy,Simple,VIP customer card design for a grocery store name"Lotus Market Hall", Chinese name"福润商场“.Major color should be Dark red. This design is based on a VIP gift card project, which means design should consider about the back side with magnetic strip area and mostly it will be plastic material.

Target Market(s)

Rich Customers

Industry/Entity Type

Grocery Store

Contact Information for Business Card

People actually put more than $1000 into the card for shopping

Font styles to use
Serif
Sans Serif
Decorative
Script
Other font styles liked:
• Fancy

Colors
ec1f27
fbed22

Requirements
Must have
• Red color
Nice to have
• Better logo transformation.

```html
<!DOCTYPE html>
<html lang="en">
<head>
<meta charset="utf-8">
<title>Lotus Market Hall VIP Card</title>
<link href="https://fonts.googleapis.com/css2?family=Roboto:wght@300;400;500;700&family=Noto+Sans+SC:wght@300;400&display=swap" rel="stylesheet">
<style>
  :root {
    --card-yellow: #fbed00;
    --brand-red: #ec1f27;
    --ink: #111111;
    --fine-print: #8a8a40;
    --note-red: #f5a623;
    --page: #ffffff;
  }
  html, body {
    margin: 0;
    width: 1200px;
    height: 1200px;
    overflow: hidden;
    background: var(--page);
    font-family: "Roboto", Arial, sans-serif;
  }
  .sheet { position: relative; width: 1200px; height: 1200px; }

  .card {
    position: absolute;
    width: 584px;
    height: 363px;
    background: var(--card-yellow);
    border-radius: 18px;
    overflow: hidden;
    transform-origin: top left;
  }
  .card--small { transform: scale(0.8); }

  /* Front */
  .brand {
    position: absolute;
    top: 100px;
    left: 0; right: 0;
    display: flex;
    justify-content: center;
    align-items: center;
    gap: 10px;
  }
  .brand__dot {
    width: 40px; height: 40px;
    border-radius: 50%;
    background: var(--brand-red);
  }
  .brand__name {
    font-size: 24px;
    font-weight: 500;
    color: var(--ink);
  }
  .brand-cn {
    position: absolute;
    top: 193px; left: 0; right: 0;
    text-align: center;
    font-family: "Noto Sans SC", sans-serif;
    font-weight: 300;
    font-size: 34px;
    letter-spacing: 1px;
    color: var(--brand-red);
  }
  .tier {
    position: absolute;
    top: 258px; left: 0; right: 0;
    text-align: center;
    font-size: 29px;
    font-weight: 700;
    color: var(--ink);
  }
  .note {
    position: absolute;
    top: 328px; left: 0; right: 0;
    text-align: center;
    font-size: 12.5px;
    font-weight: 300;
    color: var(--note-red);
  }

  /* Back */
  .mag-stripe {
    position: absolute;
    top: 38px; left: 0;
    width: 100%; height: 60px;
    background: var(--ink);
  }
  .holder {
    position: absolute;
    top: 160px; left: 0; right: 0;
    text-align: center;
    font-size: 30px;
    font-weight: 400;
    letter-spacing: 1.5px;
    color: var(--ink);
  }
  .terms {
    position: absolute;
    top: 244px; left: 21px; right: 16px;
    margin: 0;
    font-size: 13px;
    line-height: 16px;
    font-weight: 300;
    text-align: justify;
    color: var(--fine-print);
  }

  .card--top-front { left: 94px; top: 115px; z-index: 2; box-shadow: 0 22px 40px rgba(0,0,0,0.22); }
  .card--top-back { left: 512px; top: 345px; z-index: 1; box-shadow: 0 22px 40px rgba(0,0,0,0.22); }
  .card--bottom-front { left: 94px; top: 830px; }
  .card--bottom-back { left: 628px; top: 830px; }
</style>
</head>
<body>
<main class="sheet">

  <section class="card card--top-front" aria-label="Card front">
    <div class="brand"><span class="brand__dot"></span><span class="brand__name">Lotus Market Hall</span></div>
    <div class="brand-cn">福润商场</div>
    <div class="tier">V.I.P.</div>
    <div class="note">People actually put more than $1000 into the card for shopping</div>
  </section>

  <section class="card card--top-back" aria-label="Card back">
    <div class="mag-stripe"></div>
    <div class="holder">JONAH REED</div>
    <p class="terms">This "Card" contains value which may be used to purchase goods with the exception of other Cards. Please present it to a sales associate at the time of purchase and amounts will be deducted from the Card balance. This Card may not be redeemed for cash and the unused value remains on the Card. Merchant is not responsible for lost, stolen or damaged Cards or any unauthorized use.</p>
  </section>

  <section class="card card--small card--bottom-front" aria-label="Card front">
    <div class="brand"><span class="brand__dot"></span><span class="brand__name">Lotus Market Hall</span></div>
    <div class="brand-cn">福润商场</div>
    <div class="tier">V.I.P.</div>
    <div class="note">People actually put more than $1000 into the card for shopping</div>
  </section>

  <section class="card card--small card--bottom-back" aria-label="Card back">
    <div class="mag-stripe"></div>
    <div class="holder">JONAH REED</div>
    <p class="terms">This "Card" contains value which may be used to purchase goods with the exception of other Cards. Please present it to a sales associate at the time of purchase and amounts will be deducted from the Card balance. This Card may not be redeemed for cash and the unused value remains on the Card. Merchant is not responsible for lost, stolen or damaged Cards or any unauthorized use.</p>
  </section>

</main>
</body>
</html>
```